GJ & DW Fencing Pty Ltd

We already have an existing logo created by Pixel Harbour however we have restructured to a company. We would like someone to add Pty Ltd to our business name please.

Colors

Designer to choose only greyscale colors for use in the design.

```html
<!DOCTYPE html>
<html lang="en">
<head>
<meta charset="UTF-8">
<title>GJ &amp; DW Fencing Pty Ltd — Business Card</title>
<link href="https://fonts.googleapis.com/css2?family=Poppins:wght@400;500;600&display=swap" rel="stylesheet">
<style>
  :root {
    --backdrop: #1b1b1b;
    --card: #262626;
    --card-edge: #303030;
    --ink: #ffffff;
    --ink-soft: #d6d6d6;
    --ink-muted: #8a8a8a;
    --rule: #5a5a5a;
  }
  * { margin: 0; padding: 0; box-sizing: border-box; }
  html, body {
    width: 1200px; height: 800px; overflow: hidden;
    background: var(--backdrop);
    font-family: "Poppins", sans-serif;
  }
  .stage {
    position: relative; width: 1200px; height: 800px;
    display: flex; align-items: center; justify-content: center; gap: 60px;
  }
  .card {
    position: relative; width: 510px; height: 292px;
    background: var(--card);
    border: 1px solid var(--card-edge);
    border-radius: 3px;
    color: var(--ink);
  }
  .card--front { display: flex; align-items: center; justify-content: center; }
  .wordmark {
    font-family: "Poppins", sans-serif;
    font-weight: 600;
    color: var(--ink);
    letter-spacing: 0.5px;
    white-space: nowrap;
  }
  .card--front .wordmark { font-size: 30px; }
  .card--back .wordmark {
    position: absolute; top: 36px; right: 34px; font-size: 19px;
  }
  .address {
    position: absolute; right: 34px; top: 142px;
    text-align: right; font-size: 11.5px; line-height: 1.35; color: var(--ink-soft);
  }
  .address .company { color: var(--ink-muted); }
  .rule-long {
    position: absolute; left: 150px; right: 34px; top: 198px;
    height: 1px; background: var(--rule);
  }
  .person { position: absolute; left: 34px; top: 172px; }
  .person .name { font-size: 15px; font-weight: 500; color: var(--ink-muted); }
  .person .role { font-size: 11px; color: var(--ink-soft); }
  .rule-short {
    position: absolute; left: 34px; width: 110px; top: 218px;
    height: 1px; background: var(--rule);
  }
  .contact { position: absolute; left: 34px; top: 226px; list-style: none; }
  .contact li {
    display: flex; align-items: center; gap: 9px;
    font-size: 11.5px; line-height: 16px; color: var(--ink-soft);
  }
  .contact svg { width: 9px; height: 9px; fill: var(--ink-muted); flex: none; }
</style>
</head>
<body>
<main class="stage">
  <section class="card card--front" aria-label="Card front">
    <span class="wordmark">GJ &amp; DW Fencing Pty Ltd</span>
  </section>

  <section class="card card--back" aria-label="Card back">
    <span class="wordmark">GJ &amp; DW Fencing Pty Ltd</span>

    <address class="address">
      <span class="company">GJ &amp; DW Fencing Pty Ltd</span><br>
      PO Box 418<br>
      Merredin WA 6415
    </address>

    <div class="rule-long"></div>

    <div class="person">
      <div class="name">Daniel Hayes</div>
      <div class="role">President</div>
    </div>

    <div class="rule-short"></div>

    <ul class="contact">
      <li>
        <svg viewBox="0 0 10 10" aria-hidden="true"><path d="M2 0.5l1.6 2.2-1 1c.6 1.3 1.5 2.2 2.7 2.8l1-1 2.2 1.6-.8 1.8C4.5 8.7 1.3 5.5 0.2 1.3z"/></svg>
        Tom 0400 128 455
      </li>
      <li>
        <svg viewBox="0 0 10 10" aria-hidden="true"><path d="M0 2h10v6H0z M0.6 2.4L5 5.6 9.4 2.4" stroke="#262626" stroke-width="0.8"/></svg>
        office@gjdwfencing.com
      </li>
      <li>
        <svg viewBox="0 0 10 10" aria-hidden="true"><circle cx="5" cy="5" r="4.5"/><path d="M0.5 5h9M5 0.5c-2 2.5-2 6.5 0 9M5 0.5c2 2.5 2 6.5 0 9" stroke="#262626" stroke-width="0.7" fill="none"/></svg>
        www.gjdwfencing.com
      </li>
    </ul>
  </section>
</main>
</body>
</html>
```